Redesign of business card for Cedar Ridge Mechanical

We are looking for a new design for our business cards for Cedar Ridge Mechanical. We are a plumbing & HVAC construction company, operating on the West Coast of Canada and USA. Logo attached.
Industry/Entity Type
Construction - Plumbing & HVAC
Contact Information for Business Card
Name, address, phone numbers, email, website address
Look and feel
Each slider illustrates characteristics of the customer's brand and the style your logo design should communicate.

```html
<!DOCTYPE html>
<html lang="en">
<head>
<meta charset="utf-8">
<title>Cedar Ridge Mechanical — Business Card</title>
<link rel="stylesheet" href="https://fonts.googleapis.com/css2?family=Montserrat:wght@400;500;700&family=Oswald:wght@500&display=swap">
<style>
  :root {
    --stage: #1d1d1f;
    --card-white: #ffffff;
    --card-black: #1a1a1a;
    --card-back: #232323;
    --accent-grey: #9a9a9a;
    --faint: #2c2c2c;
    --ink-dark: #1a1a1a;
    --ink-light: #ffffff;
    --muted: #8c8c8c;
  }
  * { margin: 0; padding: 0; box-sizing: border-box; }
  html, body { width: 1200px; height: 801px; overflow: hidden; background: var(--stage); }
  .stage { position: relative; width: 1200px; height: 801px; }
  .card {
    position: absolute; width: 550px; height: 314px; border-radius: 22px; overflow: hidden;
    font-family: "Montserrat", sans-serif;
  }
  .card--front { left: 40px; top: 150px; background: var(--card-white); }
  .card--back { left: 610px; top: 337px; background: var(--card-back); }
  .front-wave { position: absolute; inset: 0; width: 100%; height: 100%; }
  .brand {
    position: absolute; display: flex; align-items: center; gap: 10px;
    font-family: "Oswald", sans-serif; font-weight: 500; text-transform: uppercase; letter-spacing: 1px;
    white-space: nowrap; z-index: 1;
  }
  .brand__square { border: 3px solid currentColor; border-radius: 4px; }
  .card--front .brand { right: 30px; top: 30px; color: var(--ink-dark); font-size: 21px; }
  .card--front .brand__square { width: 26px; height: 26px; }
  .holder { position: absolute; left: 32px; top: 96px; color: var(--ink-dark); z-index: 1; }
  .holder__name { font-weight: 700; font-size: 19px; letter-spacing: 1px; text-transform: uppercase; }
  .holder__name span { color: var(--muted); }
  .holder__role { font-size: 14px; margin-top: 2px; }
  .contact { position: absolute; left: 32px; top: 196px; color: var(--ink-light); font-size: 13px; line-height: 1.3; z-index: 1; }
  .contact__address { margin-bottom: 8px; }
  .contact__line { display: flex; align-items: center; gap: 7px; }
  .contact__line svg { width: 11px; height: 11px; fill: var(--ink-light); flex: none; }
  .back-faint { position: absolute; left: 40px; top: 26px; width: 470px; height: 262px; border: 26px solid var(--faint); border-radius: 36px; }
  .card--back .brand { left: 50%; top: 50%; transform: translate(-50%, -50%); color: var(--ink-light); font-size: 34px; gap: 14px; }
  .card--back .brand__square { width: 40px; height: 40px; border-width: 4px; }
</style>
</head>
<body>
<main class="stage">
  <section class="card card--front">
    <svg class="front-wave" viewBox="0 0 550 314" preserveAspectRatio="none" aria-hidden="true">
      <path d="M0,160 C200,160 300,150 380,120 C450,95 500,86 550,84" fill="none" stroke="var(--accent-grey)" stroke-width="7"/>
      <path d="M0,172 C200,172 300,162 380,132" fill="none" stroke="var(--card-black)" stroke-width="2"/>
      <path d="M0,180 C200,180 300,170 380,140 C450,115 500,106 550,104 L550,314 L0,314 Z" fill="var(--card-black)"/>
    </svg>
    <div class="brand"><span class="brand__square"></span>Cedar Ridge Mechanical</div>
    <div class="holder">
      <p class="holder__name">Daniel <span>Harper</span></p>
      <p class="holder__role">Manager</p>
    </div>
    <div class="contact">
      <p class="contact__address">Your address, city<br>state, ZIP 0000</p>
      <p class="contact__line"><svg viewBox="0 0 24 24"><path d="M6.6 10.8a15 15 0 0 0 6.6 6.6l2.2-2.2c.3-.3.7-.4 1-.2 1.1.4 2.3.6 3.6.6.6 0 1 .4 1 1V20c0 .6-.4 1-1 1A17 17 0 0 1 3 4c0-.6.4-1 1-1h3.5c.6 0 1 .4 1 1 0 1.3.2 2.5.6 3.6.1.3 0 .7-.2 1z"/></svg>123-456-2100</p>
      <p class="contact__line"><svg viewBox="0 0 24 24"><path d="M2 5h20v14H2zm2 2v.5l8 5 8-5V7z"/></svg>hello@cedarridge.example</p>
      <p class="contact__line"><svg viewBox="0 0 24 24"><circle cx="12" cy="12" r="10"/></svg>www.cedarridge.example</p>
    </div>
  </section>

  <section class="card card--back">
    <div class="back-faint" aria-hidden="true"></div>
    <div class="brand"><span class="brand__square"></span>Cedar Ridge Mechanical</div>
  </section>
</main>
</body>
</html>
```